Cat-products company needs smart, yet endearing, business card

We need a business card design for a new, but up-and-running, business based in Honolulu, Hawaii. The business is Purrnest Nook Co. Our first product is the most environmentally-friendly cat grass kit ever seen on the planet. Future products, currently in the R&D phase, will include a variety of exciting cat scratchers. We also do consulting work to help apartment-dwellers make their home more cat-friendly and, in the future, plan on doing full, custom installs of structure to create high walkways for cats.

Target Market(s)

Middle-aged, apartment-dwelling, middle-class workers who own 1 or more cats and who dote on them.

Industry/Entity Type

Pet Care

Contact Information for Business Card

A striking, professional, yet warm and friendly design is what we're after.

Font styles to use
Serif
Sans Serif
Other font styles liked:
• Comfortaa

Colors

Designer to choose colors to be used in the design.

Requirements
Must have
• The company logo: (see attachment)
• The company name: Purrnest Nook Co
• The web address: www.purrnestnookco.com
• Email: support@purrnestnookco.com
• Phone: +1 (808) 571 6023
• Update (Fri Jun 30 3017 7:45pm Hawaii Time) I would like, is possible, uploaded picture of the cat grass kit on the back of the card with some text along the lines of: Purrnest Nook Co - Maker Of The Leafiest Feline Sprout Set Yet
Nice to have
• A cat picture, cartoon, real or silhouette that illustrates cats in action and/or relaxing; ie using the apartment space to live, play and relax in and being well-contented.
• Most of the website is done in the font: Comfortaa. It might be nice to continue using this for brand consistency.
Should not have
• Hard-to-read fonts.

```html
<!DOCTYPE html>
<html lang="en">
<head>
<meta charset="utf-8">
<title>Purrnest Nook Co – Business Card</title>
<link href="https://fonts.googleapis.com/css2?family=Comfortaa:wght@700&family=Josefin+Sans:wght@400;600&family=Roboto:wght@700&display=swap" rel="stylesheet">
<style>
  :root {
    --backdrop: #2a2a2a;
    --card-white: #ffffff;
    --brand-yellow: #f7b21c;
    --brand-yellow-light: #f9c230;
    --brand-brown: #5b3b36;
    --ink-light: #ffffff;
  }
  * { margin: 0; padding: 0; box-sizing: border-box; }
  html, body { width: 1200px; height: 1000px; overflow: hidden; }
  body {
    background: var(--backdrop);
    position: relative;
    font-family: "Josefin Sans", sans-serif;
  }
  .card {
    position: absolute;
    left: 240px;
    width: 720px;
    height: 410px;
    border-radius: 34px;
    overflow: hidden;
    background: var(--card-white);
  }
  .card--front { top: 70px; }
  .card--back { top: 520px; }
  .card__shapes {
    position: absolute;
    inset: 0;
    width: 100%;
    height: 100%;
  }
  .brand-name {
    position: absolute;
    display: flex;
    align-items: center;
    gap: 14px;
    font-family: "Comfortaa", sans-serif;
    font-weight: 700;
    color: var(--brand-yellow);
    line-height: 1.05;
  }
  .brand-name__mark {
    width: 46px;
    height: 46px;
    background: var(--brand-brown);
    border-radius: 6px;
    flex: none;
  }
  .card--front .brand-name { left: 210px; top: 120px; font-size: 34px; }
  .card--back .brand-name { left: 60px; top: 170px; font-size: 32px; }

  .contact {
    position: absolute;
    left: 452px;
    top: 78px;
    color: var(--ink-light);
  }
  .contact__name {
    font-family: "Roboto", sans-serif;
    font-weight: 700;
    font-size: 24px;
    letter-spacing: 0.5px;
  }
  .contact__role {
    font-family: "Roboto", sans-serif;
    font-weight: 700;
    font-size: 12px;
    margin-top: 2px;
  }
  .contact__address {
    margin-top: 52px;
    font-size: 15px;
    line-height: 1.45;
    letter-spacing: 0.4px;
  }
  .contact__list {
    list-style: none;
    margin-top: 22px;
    font-size: 15px;
    letter-spacing: 0.4px;
  }
  .contact__list li {
    display: flex;
    align-items: center;
    gap: 12px;
    line-height: 1.5;
  }
  .contact__icon { width: 12px; height: 12px; flex: none; }
</style>
</head>
<body>

  <section class="card card--front" aria-label="Card front">
    <svg class="card__shapes" viewBox="0 0 720 410" preserveAspectRatio="none" aria-hidden="true">
      <line x1="0" y1="342" x2="720" y2="214" stroke="var(--brand-brown)" stroke-width="7"/>
      <polygon points="0,356 720,228 720,410 0,410" fill="var(--brand-yellow)"/>
    </svg>
    <div class="brand-name"><span class="brand-name__mark"></span>Purrnest Nook Co</div>
  </section>

  <section class="card card--back" aria-label="Card back">
    <svg class="card__shapes" viewBox="0 0 720 410" preserveAspectRatio="none" aria-hidden="true">
      <defs>
        <linearGradient id="panelGradient" x1="0" y1="0" x2="1" y2="1">
          <stop offset="0" stop-color="var(--brand-yellow-light)"/>
          <stop offset="1" stop-color="var(--brand-yellow)"/>
        </linearGradient>
      </defs>
      <line x1="408" y1="0" x2="474" y2="410" stroke="var(--brand-brown)" stroke-width="6"/>
      <polygon points="418,0 720,0 720,410 484,410 436,110 424,122 432,86" fill="url(#panelGradient)"/>
    </svg>
    <div class="brand-name"><span class="brand-name__mark"></span>Purrnest Nook Co</div>

    <div class="contact">
      <p class="contact__name">NOELANI BROOKS</p>
      <p class="contact__role">Director</p>
      <p class="contact__address">Your Street Address,<br>Honolulu, 96813</p>
      <ul class="contact__list">
        <li>
          <svg class="contact__icon" viewBox="0 0 12 12" aria-hidden="true"><path d="M2 1l2 0 1 3-1.5 1a6 6 0 0 0 3.5 3.5L8 7l3 1v2a1 1 0 0 1-1 1A9 9 0 0 1 1 2a1 1 0 0 1 1-1z" fill="#fff"/></svg>
          +1 (808) 571 6023
        </li>
        <li>
          <svg class="contact__icon" viewBox="0 0 12 12" aria-hidden="true"><rect x="0.5" y="2" width="11" height="8" fill="#fff"/><path d="M0.5 2l5.5 4.5L11.5 2" fill="none" stroke="#f7b21c" stroke-width="1"/></svg>
          support@purrnestnookco.com
        </li>
        <li>
          <svg class="contact__icon" viewBox="0 0 12 12" aria-hidden="true"><circle cx="6" cy="6" r="5.5" fill="#fff"/><path d="M0.5 6h11M6 0.5c-2.5 3-2.5 8 0 11M6 0.5c2.5 3 2.5 8 0 11" fill="none" stroke="#f7b21c" stroke-width="0.8"/></svg>
          www.purrnestnookco.com
        </li>
      </ul>
    </div>
  </section>

</body>
</html>
```